New Webpage for High Class Expert Witness Services Company

We are looking for a minimalist design for a webpage that just has our logo and an entry form offer to connect with one of our Liaisons.
The entry form should just ask for Name, Email, Contact Info and Description of Project.

Company Name is: The Marlowe Crest Advisory Services

Number of Pages Required

1 page

```html
<!DOCTYPE html>
<html lang="en">
<head>
<meta charset="utf-8">
<title>Marlowe Crest Advisory Services — Connect with a Liaison</title>
<link href="https://fonts.googleapis.com/css2?family=Cinzel:wght@400;600&family=Roboto:wght@400&display=swap" rel="stylesheet">
<style>
  :root {
    --bg-dark: #0f0f0f;
    --bg-mid: #1a1a1a;
    --text-white: #f4f4f4;
    --text-muted: #8f8f8f;
    --silver: #c9c9c9;
    --field-border: #9a9a9a;
    --panel-border: #5a5a5a;
    --field-bg: #0c0c0c;
    --button-light: #dcdcdd;
    --button-dark: #a2a2a5;
    --button-text: #111111;
  }
  * { box-sizing: border-box; margin: 0; padding: 0; }
  html, body { width: 1200px; height: 742px; overflow: hidden; }
  body {
    position: relative;
    background: linear-gradient(120deg, var(--bg-mid) 0%, var(--bg-dark) 45%, var(--bg-mid) 100%);
    color: var(--text-white);
    font-family: "Roboto", Arial, sans-serif;
  }
  .brand {
    position: absolute; left: 114px; top: 44px;
    display: flex; align-items: center; gap: 14px;
  }
  .brand-mark { width: 44px; height: 44px; background: var(--silver); }
  .brand-name {
    font-family: "Cinzel", Georgia, serif; font-weight: 400;
    font-size: 22px; line-height: 26px; letter-spacing: 1px;
    color: var(--silver);
  }
  .hero { position: absolute; left: 111px; top: 218px; }
  .hero-eyebrow {
    font-family: "Cinzel", Georgia, serif; font-size: 15.5px;
    letter-spacing: 1.6px; color: var(--text-muted);
  }
  .hero-title {
    margin-top: 26px; margin-left: 3px;
    border-left: 1px solid #5c5c5c;
    padding-left: 22px;
    font-family: "Cinzel", Georgia, serif; font-weight: 400;
    font-size: 51px; line-height: 51px; letter-spacing: 1.5px;
    color: var(--text-white);
  }
  .liaison-panel {
    position: absolute; left: 715px; top: 124px;
    width: 378px; height: 437px;
    border: 1px solid var(--panel-border);
    background: rgba(12,12,12,0.55);
  }
  .panel-title {
    position: absolute; left: 0; right: 0; top: 34px; text-align: center;
    font-family: "Cinzel", Georgia, serif; font-size: 25px; font-weight: 400;
    letter-spacing: 0.3px; color: var(--text-white);
  }
  .field {
    position: absolute; left: 45px; width: 294px; height: 42px;
    background: var(--field-bg); border: 1px solid var(--field-border);
    color: var(--text-white); font-family: "Roboto", Arial, sans-serif;
    font-size: 13px; padding: 0 17px;
  }
  .field::placeholder { color: var(--text-white); opacity: 1; }
  .field-name { top: 84px; }
  .field-email { top: 142px; }
  .field-phone { top: 196px; }
  .field-description { top: 253px; height: 88px; padding-top: 11px; resize: none; }
  .submit-button {
    position: absolute; left: 45px; top: 354px; width: 297px; height: 44px;
    border: none;
    background: linear-gradient(105deg, var(--button-light) 0%, var(--button-light) 38%, var(--button-dark) 62%, var(--button-dark) 100%);
    font-family: "Cinzel", Georgia, serif; font-weight: 600; font-size: 15px;
    letter-spacing: 0.5px; color: var(--button-text);
  }
  .site-footer {
    position: absolute; left: 114px; top: 673px;
    font-size: 12.5px; color: var(--text-muted);
  }
</style>
</head>
<body>
  <header class="brand">
    <span class="brand-mark"></span>
    <span class="brand-name">Marlowe Crest<br>Advisory Services</span>
  </header>

  <section class="hero">
    <p class="hero-eyebrow">MARLOWE CREST ADVISORY SERVICES</p>
    <h1 class="hero-title">SEAMLESS<br>MEDICAL EXPERT<br>INTEGRATION</h1>
  </section>

  <form class="liaison-panel">
    <h2 class="panel-title">Connect with a Liaison</h2>
    <input class="field field-name" type="text" placeholder="Name*">
    <input class="field field-email" type="email" placeholder="Email*">
    <input class="field field-phone" type="tel" placeholder="Phone number*">
    <textarea class="field field-description" placeholder="Description of Project"></textarea>
    <button class="submit-button" type="submit">SUBMIT</button>
  </form>

  <footer class="site-footer">© 2026 Marlowe Crest Advisory Services. All Rights Reserved</footer>
</body>
</html>
```